Specialised investor in e-mobility and energy wants business card design

We need a business card design that fits our existing corporate design. <The look and feel must be 'sharp'/'clean', dynamic, communicate momentum, professionalism etc (as one would imagine from a firm in the financial sector). We like the idea of a reverse-side of the card that includes the logo, and the name and contact details on the other. We expect the deliverable to be whatever format might be required to be able to get cards printed directly by a service such as kelmo press. Our website is www.zub.capital

```html
<!DOCTYPE html>
<html lang="en">
<head>
<meta charset="utf-8">
<title>ZUB Capital – Business Card</title>
<link rel="stylesheet" href="https://fonts.googleapis.com/css2?family=Montserrat:wght@400;500;700;800&display=swap">
<style>
  :root {
    --stage: #2b2e33;
    --forest: #2f5123;
    --forest-card: #33502a;
    --lime: #7cc242;
    --paper: #ffffff;
    --ink: #2f5123;
  }
  * { box-sizing: border-box; margin: 0; padding: 0; }
  html, body { width: 1200px; height: 952px; overflow: hidden; }
  body {
    background: var(--stage);
    font-family: "Montserrat", sans-serif;
    position: relative;
  }
  .card {
    position: absolute;
    width: 520px;
    height: 297px;
    top: 327px;
    border-radius: 3px;
    overflow: hidden;
    box-shadow: 0 12px 30px rgba(0,0,0,.45);
  }
  .card--back { left: 50px; background: var(--forest-card); }
  .card--front { left: 630px; background: var(--paper); }

  .wordmark {
    position: absolute;
    font-weight: 500;
    letter-spacing: .5px;
    white-space: nowrap;
  }
  .card--back .wordmark { left: 110px; top: 100px; font-size: 44px; color: var(--paper); }
  .card--front .wordmark { left: 36px; top: 96px; font-size: 36px; color: var(--ink); }

  .rule { position: absolute; height: 5px; }
  .rule--lead { left: 30px; width: 236px; top: 205px; background: var(--lime);
    clip-path: polygon(0 0, 100% 0, 97% 100%, 0 100%); }
  .rule--trail { left: 256px; width: 226px; top: 218px;
    clip-path: polygon(4% 0, 100% 0, 100% 100%, 0 100%); }
  .card--back .rule--trail { background: var(--paper); }
  .card--front .rule--trail { background: var(--forest); }

  .contact { position: absolute; left: 300px; top: 58px; color: var(--ink); }
  .contact__name { font-weight: 800; font-size: 17px; letter-spacing: .5px; }
  .contact__role { font-size: 10px; margin-top: 1px; }
  .contact__divider { width: 92px; height: 2px; background: var(--lime); margin: 5px 0 8px; }
  .contact__list { list-style: none; }
  .contact__item { display: flex; align-items: center; font-size: 10.5px; height: 19px; white-space: nowrap; }
  .contact__icon { width: 14px; height: 14px; margin-right: 7px; flex: none; }
</style>
</head>
<body>

<section class="card card--back" aria-label="Card back">
  <div class="wordmark">ZUB Capital</div>
  <div class="rule rule--lead"></div>
  <div class="rule rule--trail"></div>
</section>

<section class="card card--front" aria-label="Card front">
  <div class="wordmark">ZUB Capital</div>
  <div class="rule rule--lead"></div>
  <div class="rule rule--trail"></div>

  <div class="contact">
    <div class="contact__name">MARA KELLER</div>
    <div class="contact__role">Manager</div>
    <div class="contact__divider"></div>
    <ul class="contact__list">
      <li class="contact__item">
        <svg class="contact__icon" viewBox="0 0 14 14"><rect width="14" height="14" rx="3" fill="#7cc242"/><path d="M4 3.5c.5-.4 1-.4 1.3 0l.8 1.2c.2.4.1.8-.2 1l-.5.4c.4.9 1.1 1.6 2 2l.4-.5c.3-.3.7-.4 1-.2l1.2.8c.4.3.4.8 0 1.3-.6.7-1.5.9-2.4.4C5.9 9.1 4.9 8.1 4.1 6.4c-.5-1-.4-2.1-.1-2.9z" fill="#fff"/></svg>
        +43 70000 4821
      </li>
      <li class="contact__item">
        <svg class="contact__icon" viewBox="0 0 14 14"><rect width="14" height="14" rx="3" fill="#7cc242"/><rect x="3" y="4.2" width="8" height="5.6" fill="none" stroke="#fff" stroke-width="1"/><path d="M3 4.5 7 7.5 11 4.5" fill="none" stroke="#fff" stroke-width="1"/></svg>
        mara@zub.capital
      </li>
      <li class="contact__item">
        <svg class="contact__icon" viewBox="0 0 14 14"><rect width="14" height="14" rx="3" fill="#7cc242"/><path d="M7 2.8a3 3 0 0 1 3 3c0 2.2-3 5.4-3 5.4S4 8 4 5.8a3 3 0 0 1 3-3z" fill="#fff"/><circle cx="7" cy="5.8" r="1.1" fill="#7cc242"/></svg>
        Graz, Austria
      </li>
      <li class="contact__item">
        <svg class="contact__icon" viewBox="0 0 14 14"><rect width="14" height="14" rx="3" fill="#7cc242"/><path d="M4 3.5 10.5 6 7.8 7 9.8 10 8.8 10.7 6.8 7.7 5.2 9.8z" fill="#fff"/></svg>
        www.zub.capital
      </li>
    </ul>
  </div>
</section>

</body>
</html>
```